Health and wellnes company needs business cards

We are a Health and wellness business just relocated to Spain. Here nobody knows our business so we would like to put some of our services on the card. Clean design with logo.

Contact Information for Business Card

Brightmeadow
Paula & Oskar Dunbeck
Calle del Almendro 57
Villamar del Río
Mobile: 0046 731 402687
info@brightmeadow.example

Font styles to use
Serif

Colors
85cae6
85acd3
b768aa

Requirements
Must have
• these Services somewhere on the card
• - Private or group yoga
• - Reconnective healing
• - Kitesurfing lessons
• - Massage
• LOgo somewhere
Nice to have
• Colours that go with the logo please

```html
<!DOCTYPE html>
<html lang="en">
<head>
<meta charset="utf-8">
<title>Brightmeadow – Business Card</title>
<link href="https://fonts.googleapis.com/css2?family=Marcellus&family=Mulish:wght@400;600&display=swap" rel="stylesheet">
<style>
  :root {
    --teal: #6cc3c4;
    --navy: #1d3a6b;
    --ink: #2b2b2b;
    --rule: #8a8a8a;
    --paper: #ffffff;
    --backdrop: #e9e7e4;
  }
  * { box-sizing: border-box; margin: 0; padding: 0; }
  html, body { width: 1200px; height: 716px; overflow: hidden; }
  body {
    background: var(--backdrop);
    font-family: "Mulish", Arial, sans-serif;
    position: relative;
  }
  .card {
    position: absolute;
    top: 198px;
    width: 540px;
    height: 320px;
    box-shadow: 0 6px 18px rgba(0,0,0,0.18);
    overflow: hidden;
  }
  /* Back side */
  .card-back { left: 30px; background: var(--teal); }
  .back-brand {
    position: absolute;
    left: 0; right: 0; top: 118px;
    display: flex; align-items: center; justify-content: center; gap: 14px;
    font-family: "Marcellus", Georgia, serif;
    font-size: 34px;
    letter-spacing: 2px;
    color: var(--paper);
  }
  .back-brand .dot {
    width: 26px; height: 26px; border-radius: 50%;
    background: var(--paper);
  }
  .services {
    position: absolute;
    left: 0; right: 0; bottom: 28px;
    text-align: center;
    font-size: 12.5px;
    color: var(--paper);
    letter-spacing: 0.2px;
  }
  /* Front side */
  .card-front { left: 630px; background: var(--paper); }
  .names {
    position: absolute; left: 32px; top: 58px;
    font-family: "Marcellus", Georgia, serif;
    font-weight: 400;
    font-size: 17px; letter-spacing: 0.5px;
    color: var(--navy);
  }
  .names .second { color: var(--teal); }
  .name-rule {
    position: absolute; left: 32px; top: 86px;
    width: 240px; height: 1px; background: var(--rule);
  }
  .contact {
    position: absolute; left: 32px; top: 98px;
    list-style: none;
    font-size: 14px; color: var(--ink); line-height: 20px;
  }
  .contact li { display: flex; align-items: center; gap: 8px; }
  .contact svg { width: 12px; height: 12px; fill: var(--navy); flex: none; }
  .front-brand {
    position: absolute; right: 36px; top: 80px;
    display: flex; flex-direction: column; align-items: center; gap: 10px;
    font-family: "Marcellus", Georgia, serif;
    font-size: 24px; letter-spacing: 1px;
    color: var(--navy);
  }
  .front-brand .dot {
    width: 46px; height: 46px; border-radius: 50%;
    background: var(--teal);
  }
  .address-rule {
    position: absolute; right: 32px; top: 208px;
    width: 230px; height: 1px; background: var(--rule);
  }
  .address {
    position: absolute; right: 32px; top: 216px;
    text-align: right;
    font-size: 15px; line-height: 20px; color: var(--ink);
    font-style: normal;
  }
  .front-band { position: absolute; left: 0; bottom: 0; width: 540px; height: 60px; }
  .website {
    position: absolute; right: 32px; bottom: 7px;
    font-size: 14px; letter-spacing: 3.5px;
    color: var(--paper);
  }
</style>
</head>
<body>

<section class="card card-back" aria-label="Business card, back">
  <div class="back-brand"><span class="dot"></span><span>Brightmeadow</span></div>
  <p class="services">Private or group yoga • Reconnective healing • Kitesurfing lessons • Massage</p>
</section>

<section class="card card-front" aria-label="Business card, front">
  <h1 class="names"><span class="first">PAULA &amp; </span><span class="second">OSKAR DUNBECK</span></h1>
  <div class="name-rule"></div>
  <ul class="contact">
    <li>
      <svg viewBox="0 0 12 12" aria-hidden="true"><path d="M3 0h6a1 1 0 0 1 1 1v10a1 1 0 0 1-1 1H3a1 1 0 0 1-1-1V1a1 1 0 0 1 1-1zm0 1.5v8h6v-8z"/></svg>
      <span>0046 731 402687</span>
    </li>
    <li>
      <svg viewBox="0 0 12 12" aria-hidden="true"><path d="M0 2h12v8H0zm1 1v.4l5 3.2 5-3.2V3z"/></svg>
      <span>info@brightmeadow.example</span>
    </li>
  </ul>

  <div class="front-brand"><span class="dot"></span><span>BRIGHTMEADOW</span></div>

  <div class="address-rule"></div>
  <address class="address">Calle del Almendro 57<br>Villamar del Río</address>

  <svg class="front-band" viewBox="0 0 540 60" preserveAspectRatio="none" aria-hidden="true">
    <path d="M0 8 L220 48 Q232 38 250 32 L540 32 L540 34 L252 34 Q236 40 222 52 L0 13 Z" fill="var(--teal)"/>
    <path d="M0 14 L222 54 Q240 34 270 34 L540 34 L540 60 L0 60 Z" fill="var(--navy)"/>
  </svg>
  <p class="website">www.brightmeadow.example</p>
</section>

</body>
</html>
```